Redesign of an existing homepage

This site needs a redesign
https://www.wanderhof-kelbach.de
This page with the accommodation options is important for the customer
https://www.wanderhof-kelbach.de/gastgeber/
Till now there is a new logo. See attachment. That's all I have.
It would make sense to use the colors of the logo in the redesign.
footer.jpg.
I would put this info into the footer. The graphic (Infomaterial) is not needed.
a new menu - links.jpg
This info can be put in a new menu. Therefore the right column is gone and there is more space for the design.
NEW:
Please keep in mind that the Icons are important and shall be displayed under every accommodation

```html
<!DOCTYPE html>
<html lang="de">
<head>
<meta charset="utf-8">
<title>Tourismusverband Kelbach – Urlaub im Kelbachtal</title>
<link href="https://fonts.googleapis.com/css2?family=Roboto+Slab:wght@500;700&family=Roboto:wght@400;500;700&display=swap" rel="stylesheet">
<style>
:root{
  --blue:#0f4fa3;
  --blue-dark:#0b4a9c;
  --sky:#2aa3dc;
  --green:#78b11d;
  --text:#777;
  --white:#fff;
  --pale:#eaf4fb;
}
*{margin:0;padding:0;box-sizing:border-box}
html,body{width:1200px;height:3698px;overflow:hidden}
body{position:relative;font-family:Roboto,Arial,sans-serif;color:var(--text);background:#fff}
.abs{position:absolute}
h1,h2,h3{font-family:"Roboto Slab",Georgia,serif;font-weight:700}
p{font-size:14px;line-height:26.5px}
.justify{text-align:justify}
.btn{position:absolute;display:flex;align-items:center;justify-content:center;gap:12px;height:48px;padding:0 26px;color:#fff;font:700 15px Roboto,sans-serif;text-decoration:none;border-radius:2px;white-space:nowrap}
.btn svg{width:18px;height:14px}
.btn-green{background:var(--green)}
.btn-blue{background:var(--sky)}

.topline{left:0;top:0;width:1200px;height:3px;background:var(--green)}
.header{left:0;top:3px;width:1200px;height:124px;background:#fff;z-index:3}
.brand-circle{left:140px;top:-40px;width:200px;height:208px;border-radius:50%;background:#fff;z-index:4;display:flex;flex-direction:column;align-items:center;justify-content:flex-end;padding-bottom:38px}
.brand-mark{width:54px;height:54px;border-radius:50%;background:var(--green);margin-bottom:10px}
.brand-name{font:700 17px Roboto,sans-serif;color:var(--blue);line-height:20px;text-align:center}
.brand-sub{font:400 17px Roboto,sans-serif;color:#333;letter-spacing:.5px}
.partner{top:16px;height:64px;display:flex;align-items:center;gap:8px;font:700 15px Roboto,sans-serif;color:var(--blue);z-index:4}
.partner .sq{width:14px;height:14px;background:var(--sky)}
.partner .badge{width:86px;height:62px;background:#f0a93a}
.sep{top:22px;width:1px;height:52px;background:#ddd;z-index:4}
.nav{left:370px;top:93px;width:830px;height:45px;background:var(--blue);z-index:4;display:flex;align-items:center;font:700 12px Roboto,sans-serif;color:#fff;letter-spacing:.2px}
.nav .home{width:88px;height:45px;border-radius:0 22px 22px 22px;background:var(--sky);display:flex;align-items:center;justify-content:center;box-shadow:-4px 0 0 var(--green)}
.nav span{margin-left:24px}
.flag{display:inline-block;width:16px;height:16px;border-radius:50%;background:linear-gradient(#111 0 33%,#d00 33% 66%,#fc0 66%);vertical-align:middle;margin-right:4px}

.hero-photo{left:0;top:127px;width:1200px;height:620px;background:linear-gradient(180deg,#6c7db3 0%,#c79eb6 22%,#f3a85c 42%,#f4c26b 52%,#5b6b3a 58%,#e79c5a 72%,#b8876e 100%)}
.hero-curve{left:0;top:480px;width:1200px;height:280px}
.hero-circle{left:144px;top:202px;width:380px;height:380px;border-radius:50%;background:#fff;display:flex;flex-direction:column;align-items:center;padding-top:48px;z-index:2}
.hero-circle .mark{width:70px;height:70px;border-radius:50%;background:var(--green);margin-bottom:12px}
.hero-circle h1{font-size:27px;line-height:40px;text-align:center;color:var(--blue);white-space:nowrap}
.hero-circle h1 .plain{color:#333;font-weight:500;font-size:31px}
.hero-circle h1 .big{font-size:31px}
.hero-circle .btn{position:static;margin-top:24px;height:48px}

.about-bg{left:0;top:735px;width:1200px;height:640px;background:linear-gradient(180deg,#fff 0%,#f2f5f4 30%,#cdd5cf 70%,#b8c6a3 100%)}
.about-ring{left:142px;top:850px;width:410px;height:410px;border-radius:50%;border:12px solid var(--green);border-right-color:transparent;border-bottom-color:transparent;transform:rotate(-20deg)}
.about-photo{left:165px;top:860px;width:385px;height:385px;border-radius:50%;background:linear-gradient(160deg,#8ba8c9 0%,#5a3a25 35%,#6b4a30 60%,#c7c3b8 100%);border:6px solid #fff}
.about h2{left:593px;top:837px;font-size:42px;color:var(--blue)}
.about h2 em{font-style:normal;color:var(--green)}
.about p{left:593px;top:901px;width:462px}

.dual{left:0;top:1350px;width:1200px;height:555px}
.dual h2{font-size:40px;line-height:46px;color:#fff;white-space:nowrap}
.dual p{color:#fff}

.discover-bg{left:0;top:1905px;width:1200px;height:640px;background:linear-gradient(180deg,#fff 0%,#eef5f7 45%,#d7e7ee 70%,#f6f8f9 100%)}
.discover h2{left:143px;top:1983px;font-size:40px;line-height:51px;color:var(--blue);white-space:nowrap}
.discover h2 em{font-style:normal;color:var(--green)}
.discover p{left:143px;top:2155px;width:462px}
.video{left:668px;top:2023px;width:495px;height:397px;border-radius:12px;background:linear-gradient(180deg,#e9eef2 0%,#d5dde1 40%,#6d8a5e 62%,#c54a6e 80%,#3f6a3a 100%);box-shadow:0 6px 18px rgba(0,0,0,.15)}
.play{left:888px;top:2194px;width:56px;height:56px;border-radius:50%;background:var(--green);border:3px solid #fff;display:flex;align-items:center;justify-content:center}

.culture-bg{left:0;top:2535px;width:1200px;height:700px}
.culture h2{left:0;top:2680px;width:1200px;text-align:center;font-size:40px;color:var(--blue)}
.culture-photo{left:157px;top:2793px;width:316px;height:349px;border-radius:20px;background:linear-gradient(170deg,#d9d2c4 0%,#a89a86 45%,#3d3f4a 80%,#2a2c33 100%)}
.culture h3{left:545px;top:2790px;width:520px;font-size:20px;line-height:30px;color:#333;font-weight:500}
.culture p{left:545px;top:2862px;width:500px}

.footer{left:0;top:3230px;width:1200px;height:468px;background:var(--blue-dark);color:#fff}
.footer h4{position:absolute;font:700 18px "Roboto Slab",serif;color:#fff}
.finfo{position:absolute;display:flex;gap:16px;font-size:14px;line-height:22px}
.ficon{flex:0 0 36px;width:36px;height:36px;border-radius:50%;background:#fff;display:flex;align-items:center;justify-content:center}
.ficon.green{background:var(--green)}
.ficon svg{width:16px;height:16px}
.fdivider{left:748px;top:3290px;width:1px;height:225px;background:rgba(255,255,255,.25)}
.brochure{left:815px;top:3350px;width:100px;height:95px;border-radius:6px;background:linear-gradient(135deg,#f3e9e4,#c9423a 50%,#e8c9a2);border:3px solid #fff}
.fbtn{left:815px;top:3462px;width:240px;height:58px;background:var(--green);color:#fff;font:700 13px Roboto,sans-serif;text-align:center;display:flex;align-items:center;justify-content:center;line-height:18px}
.copy{left:143px;top:3628px;font-size:13px;color:#fff}
.social{top:3618px;width:34px;height:34px;border-radius:50%;background:#fff;color:var(--blue);font:700 11px Roboto,sans-serif;display:flex;align-items:center;justify-content:center}
</style>
</head>
<body>

<div class="abs topline"></div>

<div class="abs hero-photo" role="img" aria-label="Sonnenuntergang über einem Fluss mit Stauwehr und Wald, spiegelnd im Wasser"></div>
<svg class="abs hero-curve" viewBox="0 0 1200 280" preserveAspectRatio="none" aria-hidden="true">
  <path d="M0 30 C250 230 700 300 1200 200 L1200 280 L0 280Z" fill="#fff"/>
  <path d="M55 90 C260 230 480 270 700 245 C540 260 260 230 55 90Z" fill="var(--green)" stroke="var(--green)" stroke-width="8"/>
  <path d="M580 262 C800 240 1010 180 1140 78 C1000 200 790 255 580 262Z" fill="var(--sky)" stroke="var(--sky)" stroke-width="8"/>
</svg>

<header class="abs header"></header>
<div class="abs brand-circle">
  <div class="brand-mark"></div>
  <div class="brand-name">TOURISMUSVERBAND</div>
  <div class="brand-sub">KELBACH</div>
</div>
<div class="abs partner" style="left:517px"><div class="badge"></div></div>
<div class="abs sep" style="left:624px"></div>
<div class="abs partner" style="left:650px"><span class="sq"></span>Bäderland</div>
<div class="abs sep" style="left:796px"></div>
<div class="abs partner" style="left:820px"><span class="sq"></span>Waldland</div>
<div class="abs sep" style="left:967px"></div>
<div class="abs partner" style="left:990px"><span class="sq" style="background:var(--green)"></span>Talverbund</div>
<nav class="abs nav">
  <div class="home">HOME</div>
  <span>GASTGEBER</span><span>KELBACHTAL</span><span>FREIZEIT</span><span>AUSFLUGSZIELE</span><span>KUNST UND KULTUR</span><span>KONTAKT</span><span><i class="flag"></i>▾</span>
</nav>

<div class="abs hero-circle">
  <div class="mark"></div>
  <h1>URLAUB IM KELBACHTAL<br><span class="plain">DEM SCHÖNSTEN</span><br><span class="big">FLECK BAYERNS</span></h1>
  <a class="btn btn-green" href="https://www.wanderhof-kelbach.de/gastgeber/">FANGEN SIE AN <svg viewBox="0 0 18 14"><path d="M1 7h15M10 1l6 6-6 6" stroke="#fff" stroke-width="2" fill="none"/></svg></a>
</div>

<section class="about">
  <div class="abs about-bg" role="img" aria-label="Helle Berglandschaft mit grünen Hängen"></div>
  <div class="abs about-ring"></div>
  <div class="abs about-photo" role="img" aria-label="Altes Holzbauernhaus mit Blumenbalkonen und Kindern auf einem Tretauto"></div>
  <h2 class="abs">ÜBER <em>UNS</em></h2>
  <p class="abs justify">Lieber Besucherinnen und Besucher,Kelbach und Umgebung haben all das, was das Leben lebenswert macht:Kultur und Natur, Lebensfreude und Genuss, freundliche und aufgeschlossene Menschen...Ob Kirchen, Brunnen oder andere Baudenkmäler – bei einem Rundgang durch die Kelbacher Ross-Stadt kann man viele liebevolle Details für sich entdecken. Für Bewegungsfreudige und Erholungssuchende gibt es "Natur pur" in und um Kelbach! Hier kann man sportlich unterwegs sein beim Radeln, Walken, Wandern, Golfen, Reiten und Baden oder einfach nur die Ruhe genießen.Freizeit und Erholung für die ganze Familie – planen Sie einen Urlaub auf dem Bauernhof, in einer Ferienwohnung oder im Hotel. Ihr Urlaub im Kelbachtal wird ein einmaliges Erlebnis!</p>
  <a class="btn btn-green" style="left:593px;top:1224px;width:181px" href="https://www.wanderhof-kelbach.de">MEHR LESEN <svg viewBox="0 0 18 14"><path d="M1 7h15M10 1l6 6-6 6" stroke="#fff" stroke-width="2" fill="none"/></svg></a>
</section>

<section class="dual abs">
  <svg class="abs" style="left:0;top:0" width="1200" height="555" viewBox="0 0 1200 555" aria-hidden="true">
    <path d="M0 235 C180 60 480 -20 760 50 C600 140 510 300 465 555 L0 555Z" fill="var(--green)" stroke="#fff" stroke-width="10"/>
    <path d="M470 555 C520 280 650 120 790 65 C920 10 1080 -5 1200 20 L1200 555Z" fill="var(--sky)" stroke="#fff" stroke-width="10"/>
  </svg>
  <h2 class="abs" style="left:146px;top:170px">FREIZEIT IM<br>KELBACHTAL</h2>
  <p class="abs justify" style="left:146px;top:281px;width:335px">Freizeit und Erholung für die ganze Familie<br>Ruhe und Erholung in der Natur genießen – verbunden mit ausgesuchten Aktivitäten. Sportlich unterwegs beim Radeln, Walken und Wandern oder einfach nur die Seele baumeln lassen.</p>
  <a class="btn btn-blue" style="left:146px;top:440px;width:181px" href="https://www.wanderhof-kelbach.de">MEHR LESEN <svg viewBox="0 0 18 14"><path d="M1 7h15M10 1l6 6-6 6" stroke="#fff" stroke-width="2" fill="none"/></svg></a>
  <h2 class="abs" style="left:732px;top:170px">AUSFLUGSZIELE</h2>
  <p class="abs justify" style="left:732px;top:233px;width:325px">Einige der schönsten Ausflugsziele Bayerns, Österreichs und Tschechiens liegen nur einen Tagesausflug entfernt. Der Naturpark Hoher Forst bietet zahlreiche Ausflugsmöglichkeiten für jedes Alter. Das Hügelviertel mit seinen charakteristischen Städten wie Lindenau und Steinfurt und auch</p>
  <a class="btn btn-green" style="left:732px;top:440px;width:181px" href="https://www.wanderhof-kelbach.de">MEHR LESEN <svg viewBox="0 0 18 14"><path d="M1 7h15M10 1l6 6-6 6" stroke="#fff" stroke-width="2" fill="none"/></svg></a>
</section>

<section class="discover">
  <div class="abs discover-bg" role="img" aria-label="Heller Hintergrund mit Wasser und Uferlandschaft"></div>
  <h2 class="abs">DAS KELBACHTAL<br><em>ENTDECKEN, ERLEBEN</em><br>UND GENIEßEN!</h2>
  <p class="abs justify">Die Ferienregion Kelbachtal zeichnet sich aus durch wunderschöne Landschaft und abwechslungsreiche Freizeitangebote.Finden Sie Ruhe und Aktivität, Kultur und Genuss... immer verbunden mit der Herzlichkeit der Gastgeber und dem positiven Lebensgefühl dieser Region. Hier kann man den Alltag vergessen und bewusst und entschleunigt das Leben genießen.Erkunden Sie die herrliche Natur bei einem gemütlichen Spaziergang oder einer Radtour durch die sanfte Hügellandschaft des Kelbachtals, vorbei an zahlreichen Sehenswürdigkeiten.</p>
  <a class="btn btn-green" style="left:143px;top:2400px;width:181px" href="https://www.wanderhof-kelbach.de">MEHR LESEN <svg viewBox="0 0 18 14"><path d="M1 7h15M10 1l6 6-6 6" stroke="#fff" stroke-width="2" fill="none"/></svg></a>
  <div class="abs video" role="img" aria-label="Video: Dorf mit Kirchturm hinter blühenden Rosen"></div>
  <div class="abs play"><svg width="20" height="22" viewBox="0 0 20 22"><path d="M3 2l15 9-15 9z" fill="#fff"/></svg></div>
</section>

<section class="culture">
  <svg class="abs culture-bg" viewBox="0 0 1200 700" preserveAspectRatio="none" aria-hidden="true">
    <path d="M0 215 C250 70 500 40 600 40 C760 40 1000 80 1200 215 L1200 700 L0 700Z" fill="var(--pale)"/>
    <path d="M195 110 C320 50 450 15 570 10 C450 30 320 70 195 110Z" stroke="var(--sky)" stroke-width="6" fill="var(--sky)"/>
    <path d="M720 10 C830 15 950 50 1035 105 C940 60 830 30 720 10Z" stroke="var(--green)" stroke-width="6" fill="var(--green)"/>
  </svg>
  <h2 class="abs">KUNST UND KULTUR</h2>
  <div class="abs culture-photo" role="img" aria-label="Familie von hinten vor einer gotischen Kathedralfassade"></div>
  <h3 class="abs">KUNST IST NICHT ALLES, ABER OHNE KUNST IST ALLES NICHTS!</h3>
  <p class="abs justify">Brauchtum, Kunst und Kultur sowie Lebensfreude haben im traditionsreichen Kelbachtal einen festen Platz. Das Kelbachtal ist reich an Sehenswürdigkeiten, die es zu entdecken gilt. Kirchen und Kapellen in Backsteingotik aus dem 14. und 15. Jhd. laden zu einem Besuch ein. Städte und Märkte zeigen sich in typischer Flusstal-Bauweise von ihrer schönsten Seite. Brunnen und Denkmäler namhafter Künstler wollen beachtet werden. Zahlreiche Museen zeigen die kulturellen Wurzeln der Region.</p>
  <a class="btn btn-green" style="left:545px;top:3073px;width:181px" href="https://www.wanderhof-kelbach.de">MEHR LESEN <svg viewBox="0 0 18 14"><path d="M1 7h15M10 1l6 6-6 6" stroke="#fff" stroke-width="2" fill="none"/></svg></a>
</section>

<footer class="abs footer">
  <h4 style="left:143px;top:60px">FVV KEL</h4>
  <div class="finfo" style="left:143px;top:112px;width:300px">
    <div class="ficon green"><svg viewBox="0 0 16 16"><path d="M8 1a5 5 0 0 0-5 5c0 4 5 9 5 9s5-5 5-9a5 5 0 0 0-5-5zm0 7a2 2 0 1 1 0-4 2 2 0 0 1 0 4z" fill="#fff"/></svg></div>
    <div>Fremdenverkehrsverein Kelbach<br>und Umgebung e. V. Marktplatz 4<br>94371 Kelbach</div>
  </div>
  <div class="finfo" style="left:143px;top:180px">
    <div class="ficon"><svg viewBox="0 0 16 16"><path d="M4 1l3 3-2 2c1 2 3 4 5 5l2-2 3 3-2 3C7 15 1 9 1 3z" fill="var(--blue)"/></svg></div>
    <div style="padding-top:7px">Tel.: 09371 / 482 1160</div>
  </div>
  <div class="finfo" style="left:143px;top:230px">
    <div class="ficon"><svg viewBox="0 0 16 16"><path d="M3 5h10v8H3zM5 2h6v3H5z" fill="var(--blue)"/></svg></div>
    <div style="padding-top:7px">Fax: 09371 / 482 1169</div>
  </div>
  <div class="finfo" style="left:457px;top:117px">
    <div class="ficon"><svg viewBox="0 0 16 16"><path d="M2 4h12v8H2z" fill="var(--blue)"/><path d="M2 4l6 5 6-5" stroke="#fff" stroke-width="1.5" fill="none"/></svg></div>
    <div style="padding-top:7px">info@kelbach-urlaub.de</div>
  </div>
  <div class="finfo" style="left:457px;top:168px">
    <div class="ficon"><svg viewBox="0 0 16 16"><circle cx="8" cy="8" r="7" fill="var(--blue)"/><path d="M8 4v4l3 2" stroke="#fff" stroke-width="1.5" fill="none"/></svg></div>
    <div style="padding-top:6px">Öffnungszeiten:<br>Mo-Fr 9:00 – 17:00 Uhr<br>Mai-Oktober:<br>Sa 9:00-12:00 Uhr</div>
  </div>
  <h4 style="left:805px;top:60px">INFOMATERIAL</h4>
</footer>
<div class="abs fdivider"></div>
<div class="abs brochure" role="img" aria-label="Broschüren und Prospekte der Region"></div>
<div class="abs fbtn">FORDERN SIE<br>INFORMATIONSMATERIAL AN</div>
<div class="abs copy">© 2025 Firmenname. Alle Rechte vorbehalten | Datenschutzrichtlinie | Nutzungsbedingungen</div>
<div class="abs social" style="left:888px">Pix</div>
<div class="abs social" style="left:932px">Cir</div>
<div class="abs social" style="left:976px">Flit</div>
<div class="abs social" style="left:1020px">Vid</div>

</body>
</html>
```